I am looking to create a newly designed website for our national leadership conference which is entitled, "The Harbor of Momentum Leadership Summit". The Harbor of Momentum Leadership Summit is a national conference for student leaders that prepares them for career leadership success. The current website can be seen at www.harborofmomentumleadershipsummit.com.

My goal for the new site is to create a more updated, fresh, hip, and exciting look that appeals to the younger generation while also maintaining are professional appeal. The color should be black, white, and gold. We want there to be live videos played and places to insert pictures for the panels as well.

I look forward to seeing you the new creations.

Requirements
Must have
• Ability to play videos on the home page and throughout the website. Also, make sure that the website shows up clearly on an zTablet.
Nice to have
• Nice look

```html
<!DOCTYPE html>
<html lang="en">
<head>
<meta charset="utf-8">
<title>The Harbor of Momentum Leadership Summit – About</title>
<link href="https://fonts.googleapis.com/css2?family=Roboto:wght@300;400;500&display=swap" rel="stylesheet">
<style>
:root{
  --gold:#b8923f;
  --gold-light:#d4b062;
  --ink:#222;
  --text:#444;
  --muted:#888;
  --bar:#1e1e1e;
  --footer:#282828;
  --line:#d6d6d6;
  --icon-bg:#e6e6e6;
}
*{margin:0;padding:0;box-sizing:border-box}
html,body{width:904px;height:1200px;overflow:hidden;background:#fff}
body{font-family:'Roboto',Arial,sans-serif;color:var(--text);position:relative}
.wrap{position:absolute;left:56px;width:792px}

.top{height:94px;position:relative}
.follow{position:absolute;left:56px;top:34px;display:flex;align-items:center;gap:2px;font-size:8px;font-weight:500;color:var(--ink)}
.follow span{margin-right:6px}
.follow i{display:block;width:22px;height:22px;background:#555}
.follow i:nth-child(2){background:#3b5998}.follow i:nth-child(3){background:#1da1f2}
.follow i:nth-child(4){background:#0e76a8}.follow i:nth-child(5){background:#c4302b}.follow i:nth-child(6){background:#8a6a4c}
.brand{position:absolute;left:50%;transform:translateX(-50%);top:14px;text-align:center}
.brand .dot{width:38px;height:38px;border-radius:50%;background:radial-gradient(circle at 40% 35%,var(--gold-light),var(--gold));margin:0 auto 6px}
.brand b{font-weight:500;font-size:12px;letter-spacing:1.5px;color:var(--ink)}
.cta{position:absolute;right:56px;top:26px;width:167px;height:40px;border-radius:20px;background:linear-gradient(#c9a24f,#a9802f);color:#fff;font-size:17px;font-weight:400;display:flex;align-items:center;justify-content:center;letter-spacing:.5px}

.nav{position:absolute;top:94px;left:0;width:904px;height:46px;background:linear-gradient(#333,#111);display:flex;padding-left:118px}
.nav a{color:#fff;font-size:11px;font-weight:500;text-decoration:none;padding:0 17px;display:flex;align-items:center;letter-spacing:.3px}
.nav a.on{background:var(--gold);padding:0 22px}

.crumb{top:166px;font-size:9px;color:#666;left:62px}
.crumb em{font-style:normal;color:var(--gold)}
.rule{top:192px;height:1px;background:var(--line)}
.title{top:208px;font-size:25px;font-weight:400;color:var(--ink);letter-spacing:.2px}

.tabs{top:259px;height:44px;border:1px solid #ccc;border-radius:22px;background:linear-gradient(#fff,#ececec);display:flex;align-items:center;padding-left:25px;gap:18px}
.tabs a{font-size:9px;font-weight:500;color:var(--ink);text-decoration:none;padding:6px 0}
.tabs a.on{background:var(--gold);color:#fff;border-radius:12px;padding:6px 16px}

.about{top:328px;width:440px}
.about h2{font-size:18px;font-weight:400;color:var(--ink);display:flex;align-items:center;gap:16px;margin-bottom:16px}
.about h2 .dot{width:40px;height:28px;border-radius:50%;background:radial-gradient(circle at 40% 40%,var(--gold-light),var(--gold))}
.about h2 em{font-style:normal;color:var(--gold)}
.about p{font-size:10.6px;font-weight:300;line-height:18px;color:var(--text)}
.about ul{list-style:none;margin-top:6px}
.about li{font-size:10.6px;font-weight:300;line-height:18px;padding-left:17px;position:relative;margin-bottom:6px}
.about li b{font-weight:400;color:var(--ink)}
.about li::before{content:"";position:absolute;left:0;top:5px;width:7px;height:7px;border:1px solid var(--gold);border-radius:50%}
.photo{position:absolute;left:515px;top:336px;width:334px;height:222px;background:linear-gradient(135deg,#5a4a3c,#3a2e26 60%,#6b5844)}

.lead{top:698px;font-size:10.6px;color:var(--ink)}
.goals{top:734px;height:320px}
.goal{position:absolute;width:230px;padding-left:58px}
.goal .ic{position:absolute;left:0;top:0;width:47px;height:47px;border-radius:50%;background:var(--icon-bg);display:flex;align-items:center;justify-content:center}
.goal h3{font-size:13px;font-weight:400;color:var(--gold);margin:10px 0 9px}
.goal p{font-size:10.6px;font-weight:300;line-height:17.5px;color:var(--text)}

.footer{position:absolute;top:1061px;left:0;width:904px;height:139px;background:var(--footer)}
.fnav{position:absolute;left:56px;top:42px;display:flex;gap:22px}
.fnav a{color:#fff;font-size:9px;font-weight:500;text-decoration:none}
.copy{position:absolute;left:56px;top:77px;font-size:9px;color:#999;line-height:16px;letter-spacing:.3px}
.fbrand{position:absolute;right:56px;top:38px;text-align:center}
.fbrand .dot{width:40px;height:40px;border-radius:50%;background:#666;margin:0 auto 8px}
.fbrand b{font-size:12px;font-weight:500;letter-spacing:1.5px;color:#777}
</style>
</head>
<body>
<header class="top">
  <div class="follow"><span>FOLLOW US</span><i></i><i></i><i></i><i></i><i></i></div>
  <div class="brand"><div class="dot"></div><b>HARBOR OF MOMENTUM</b></div>
  <a class="cta">REGISTER NOW</a>
</header>
<nav class="nav">
  <a>HOME</a><a class="on">ABOUT</a><a>CONFERENCE</a><a>REGISTER</a><a>TESTIMONIALS</a><a>Y FACTOR</a><a>VIDEOS</a><a>CONTACT</a>
</nav>

<div class="wrap crumb">HOME &nbsp;»&nbsp; <em>ABOUT</em></div>
<div class="wrap rule"></div>
<h1 class="wrap title">HARBOR OF MOMENTUM LEADERSHIP SUMMIT</h1>

<div class="wrap tabs">
  <a class="on">ABOUT</a><a>EXECUTIVE LEADERSHIP TEAM</a><a style="margin-left:12px">FACILITATORS</a><a style="margin-left:12px">MODERATORS</a><a style="margin-left:12px">BOARD OF DIRECTORS</a>
</div>

<section class="wrap about">
  <h2><span class="dot"></span><span>ABOUT <em>THE HARBOR OF MOMENTUM</em></span></h2>
  <p>The Harbor Of Momentum Leadership Experience Is A Three Day Conference That Not Only Connects Student Leaders Nationally With An Incredible Diverse Leadership Network Of Students And Professionals That Will Provide Them With The Inspiration, Leadership Development Training, And Professional Skills Needed To Take Their Personal And Leadership Experience To The Next Level, But It's A Life Changing Conference That Consists Of...</p>
  <ul>
    <li><b>Dynamic</b> keynote speakers</li>
    <li><b>Scholarly</b> workshop sessions on leadership development for student leaders</li>
    <li><b>Experts</b> with real-world leadership experience from more than 70 different Top 500 companies</li>
    <li><b>Reflection</b>, Assessment, and Group Activities with Trained Student Affair Professionals</li>
    <li><b>Tons</b> of Networking Opportunities with Students and Executives Passionate about Leadership</li>
    <li><b>Impactful</b> Service Project that teaches the importance of Service and Civic Engagement</li>
  </ul>
</section>
<div class="photo" role="img" aria-label="Photo of a speaker addressing a seated audience of students in a conference hall"></div>

<p class="wrap lead">Each of these amazing programs offered throughout the entire conference are based upon five learning objectives which are:</p>

<section class="wrap goals">
  <div class="goal" style="left:0;top:0"><div class="ic"><svg width="22" height="22" viewBox="0 0 22 22" fill="#333"><circle cx="6" cy="6" r="3"/><circle cx="16" cy="6" r="3"/><rect x="2" y="11" width="8" height="8" rx="2"/><rect x="12" y="11" width="8" height="8" rx="2"/></svg></div>
    <h3>Interpersonal Development</h3><p>Students will learn more about hemselves and how that translate into effective leadership in the 21st Century.</p></div>
  <div class="goal" style="left:280px;top:0"><div class="ic"><svg width="22" height="22" viewBox="0 0 22 22" fill="#333"><circle cx="11" cy="4" r="3"/><circle cx="4" cy="7" r="2.5"/><circle cx="18" cy="7" r="2.5"/><rect x="8" y="8" width="6" height="12" rx="1"/><rect x="1.5" y="10" width="5" height="9" rx="1"/><rect x="15.5" y="10" width="5" height="9" rx="1"/></svg></div>
    <h3>Leadership Development</h3><p>Students will learn about more than twenty different leadership skills and qualities that leaders must possess in the 21st Century in order to be effective.</p></div>
  <div class="goal" style="left:549px;top:0"><div class="ic"><svg width="22" height="22" viewBox="0 0 22 22" fill="#333"><circle cx="4" cy="6" r="2.5"/><circle cx="18" cy="6" r="2.5"/><circle cx="11" cy="3" r="2.5"/><rect x="5" y="11" width="12" height="3"/><rect x="2" y="10" width="4" height="9"/><rect x="16" y="10" width="4" height="9"/></svg></div>
    <h3>Professional Development</h3><p>Students will learn about more than fifteen professional skills that students must attain in order to evolve and experience career leadership success in the 21st Century.</p></div>
  <div class="goal" style="left:0;top:154px"><div class="ic"><svg width="22" height="22" viewBox="0 0 22 22" fill="#333"><circle cx="6" cy="4" r="2.5"/><circle cx="16" cy="4" r="2.5"/><rect x="3" y="8" width="6" height="13" rx="1"/><rect x="13" y="8" width="6" height="13" rx="1"/><rect x="8" y="11" width="6" height="2"/></svg></div>
    <h3>Socially Responsible Leaders</h3><p>Students will learn about the importance of social responsibility, ethical decision-making, civic en-gagement, social justice, and service learning.</p></div>
  <div class="goal" style="left:280px;top:154px"><div class="ic"><svg width="24" height="22" viewBox="0 0 24 22" fill="none" stroke="#333" stroke-width="1.8"><rect x="2" y="3" width="20" height="13"/><path d="M12 16v4M7 20h10" /><path d="M7 13v-3M10 13V8M13 13V9M16 13V6" /></svg></div>
    <h3>Value of Diversity</h3><p>Students will not only about the importance of diversity in the 21st Century, but they will discover how to interact, collaborate, appreciate, and lead diverse groups of people more effectively.</p></div>
</section>

<footer class="footer">
  <div class="fnav"><a>HOME</a><a>ABOUT</a><a>CONFERENCE</a><a>REGISTER</a><a>TESTIMONIALS</a><a>Y FACTOR</a><a>VIDEOS</a><a>CONTACT</a></div>
  <div class="copy">Copyright © 2015. Company Name All Right Reserved<br>Privacy Policy &nbsp;|&nbsp; Term &amp; Conditions</div>
  <div class="fbrand"><div class="dot"></div><b>HARBOR OF MOMENTUM</b></div>
</footer>
</body>
</html>
```